Etiketten für Ätherische Öle, Extrakte und Speiseöle gesucht
Zielgruppe
Wir verkaufen natürlich Produkte. Ätherische öle, Extrakte, Speise öle.
Wir verkaufen im Webshop, Korbix und auch im Betrieb.
https://www.natur-vemo.com
Wir verkaufen hauptsächlich innerhalb Italiens und Deutschland daher doppel sprachig.
Aufgabenstellung
Guten Tag
Bitte verwenden Sie! : * beispiel_10_ml_etikett_nachbau.jpg *
Da mir die kleinste Größe die wichtigste ist habe ich ein beispiel Hochgeladen. Das kleinste Etikett lässt sich öffnen und daher sind nur 7 cm ersichtlich und man muss das Etikett aufmachen.
Habe ein Beispiel Hochgeladen. Aber bitte einfach kreativ sein. *Anhang: beispiel Etikett*
Sobald ich eine Art vom kelinsten habe würde ich dies für die 2 anderen Größen übernehmen aber das man Sie irgendwie gut unterscheiden kann da dies dann komplett andere Produkte (Extrakte/Speise öl) sein werden.
Erstellung von drei unterschiedlichen Größen von Etiketten mit folgenden Eigenschaften:
Am wichtigsten ist mir das kleinste Etikett da dies auch am schwersten ist daher habe ich die anderen Größen nun gelöscht!
• 10 ml Länge: 155 mm Breite: 32 mm.
Brauche 3 unterschiedliche Grund Farben: z. B. Ätherische Öle (Grün) Extrakte (Rot) Speiseöle (gelb). Die Farben lasse ich sie entscheiden.
Die Etiketten müssen 2 Sprachen (Deutsch / Italienisch) sein deshalb muss dieses berücksichtigt werden.
Anbei finden Sie:
• Logo (Bild Logo)
• Beispiel Text ätherische Öle
• Bilder der aktuellen Flaschen
Unter https://www.natur-vemo.com/de finden Sie meine Seite
Anmerkung: Im Anhang: *Back*
Habe ich mein Logo mit Firmennamen ; Bio des Haubner Stefan
Da ich jedoch nicht alle Produkte im biologischen Anbau habe und mein Logo zu miss Verständnis führen könnte habe ich ein Bildliches Logo gemacht das ich fortan auf meinen Produkten haben möchte. Im besonderes dieses Grün das in beiden vorhanden ist versuche ich zu integrieren.
Habe selbst ein Etikett designet das aber sehr unprofessionell wirkt aber dieses Grüne das ich gerne als merkmal unterbringen würde.
Siehe Anhang: neemöl

```html
<!DOCTYPE html>
<html lang="de">
<head>
<meta charset="utf-8">
<title>Lavendel Fein – Etikett 10 ml</title>
<link rel="stylesheet" href="https://fonts.googleapis.com/css2?family=Roboto+Condensed:wght@400;700&family=Arimo&family=Sniglet:wght@800&family=Gochi+Hand&display=swap">
<style>
  :root {
    --page: #ffffff;
    --label-edge: #6e4a8a;
    --label-mid: #a8679f;
    --label-glow: #b874ad;
    --ink-light: #ffffff;
    --ink-soft: #f3e9f4;
    --ribbon: #ffffff;
    --ribbon-fold: #d9cde3;
    --ribbon-ink: #4b2a72;
    --flower-top: #6a55b8;
    --flower-mid: #9a7ccf;
    --stem: #8a9f7a;
  }
  * { box-sizing: border-box; margin: 0; padding: 0; }
  html, body { width: 1200px; height: 1200px; overflow: hidden; background: var(--page); }
  .canvas { position: relative; width: 1200px; height: 1200px; }

  .label {
    position: absolute; left: 50px; top: 391px; width: 1100px; height: 417px;
    background:
      radial-gradient(ellipse 45% 70% at 47% 50%, var(--label-glow) 0%, rgba(184,116,173,0) 100%),
      linear-gradient(90deg, var(--label-edge) 0%, var(--label-mid) 45%, var(--label-mid) 55%, var(--label-edge) 100%);
    color: var(--ink-light);
    font-family: "Roboto Condensed", "Arial Narrow", sans-serif;
    font-size: 12px; line-height: 17.5px;
    overflow: hidden;
  }
  .label p { margin: 0; }
  .label strong { font-weight: 700; }

  .column { position: absolute; }
  .column--warnings { left: 28px; width: 262px; }
  .column--usage { left: 820px; width: 268px; }

  .warning-de { top: 22px; }
  .warning-it { top: 98px; }
  .producer { top: 194px; }
  .lot { top: 350px; }
  .shelf-life { top: 372px; display: flex; gap: 6px; align-items: flex-start; line-height: 14px; }
  .shelf-life svg { flex: none; margin-top: 1px; }

  .usage-it { top: 30px; }
  .usage-de { top: 234px; }
  .usage-block + .usage-block { margin-top: 6px; }

  .center-art { position: absolute; left: 0; top: 0; width: 1100px; height: 417px; }
  .arc-title {
    font-family: "Sniglet", "Trebuchet MS", sans-serif; font-weight: 800;
    font-size: 25px; fill: var(--ink-light); letter-spacing: 0.3px;
  }
  .product-name {
    font-family: "Gochi Hand", cursive; font-size: 40px; fill: var(--ribbon-ink);
  }
  .botanical {
    position: absolute; left: 372px; width: 300px; top: 338px; text-align: center;
    font-family: "Arimo", Arial, sans-serif; font-size: 17px; line-height: 20px; color: var(--ink-soft);
  }
</style>
</head>
<body>
<div class="canvas">
  <section class="label" aria-label="Etikett Lavendel Fein">

    <svg class="center-art" viewBox="0 0 1100 417" width="1100" height="417">
      <defs>
        <linearGradient id="flowerTone" x1="0" y1="0" x2="0" y2="1">
          <stop offset="0" stop-color="var(--flower-top)"/>
          <stop offset="0.7" stop-color="var(--flower-mid)"/>
          <stop offset="1" stop-color="var(--stem)" stop-opacity="0.7"/>
        </linearGradient>
        <path id="titleArc" d="M 390 248 A 140 140 0 1 1 654 248"/>
      </defs>

      <rect class="flower-illustration" role="img" aria-label="Aquarell-Illustration von Lavendelblüten mit grünen Stielen"
            x="472" y="92" width="100" height="196" rx="34" fill="url(#flowerTone)" opacity="0.85"/>

      <text class="arc-title"><textPath href="#titleArc" startOffset="50%" text-anchor="middle">100% natürliches etherisches Öl</textPath></text>

      <g class="ribbon">
        <path d="M 394 292 L 420 286 L 420 326 L 394 332 L 406 312 Z" fill="var(--ribbon-fold)"/>
        <path d="M 650 292 L 624 286 L 624 326 L 650 332 L 638 312 Z" fill="var(--ribbon-fold)"/>
        <path d="M 410 282 Q 522 266 634 282 L 634 324 Q 522 308 410 324 Z" fill="var(--ribbon)"/>
      </g>
      <text class="product-name" x="522" y="316" text-anchor="middle">Lavendel Fein</text>
    </svg>

    <div class="botanical">
      <p>Lavanda vera</p>
      <p>Lavandula angustifolia</p>
    </div>

    <div class="column column--warnings warning-de">
      <p>Nur in der angegeben Verdünnung anwenden!<br>Nicht in die Augen oder auf die Schleimhäute bringen! Außer Reichweite von Kindern lagern. Abgefüllt in Italien</p>
    </div>
    <div class="column column--warnings warning-it">
      <p>Da usare solo diluito come da indicazione! Evitare il contatto con occhi e mucose! Tenere fuori dalla portata dei bambini. Imbottigliato in Italy</p>
    </div>
    <div class="column column--warnings producer">
      <p><strong>Bio des Haubner Stefan</strong></p>
      <p>Brunnweg 14</p>
      <p>I-39020 Talheim</p>
      <p>IVA: IT01234567890</p>
      <p>CF: HBNSTF88M12A952K</p>
      <p>Tel: +39 0471/208517 Handy: 3401186273</p>
      <p>www.natur-vemo.com</p>
      <p>info.naturvemo@mailbox.it</p>
    </div>
    <div class="column column--warnings lot">
      <p>LottoNummer/CH nummer: 123456</p>
    </div>
    <div class="column column--warnings shelf-life">
      <svg width="18" height="16" viewBox="0 0 18 16" aria-hidden="true">
        <path d="M2 6 h12 v3 a6 6 0 0 1 -12 0 Z" fill="var(--ink-light)"/>
        <path d="M12 2 L15 5" stroke="var(--ink-light)" stroke-width="1.6" fill="none"/>
        <path d="M4 3 h5 v3 h-5 Z" fill="var(--ink-light)"/>
      </svg>
      <p>Haltbar bis <strong>12 Monate</strong><br>nach der Öffnung</p>
    </div>

    <div class="column column--usage usage-it">
      <p class="usage-block"><strong>100% olio essenziale naturale.</strong> Cosmetico aromatico per la cura del corpo.</p>
      <p class="usage-block"><strong>Modo d'uso:</strong> Come olio da massaggio o olio per il corpo: versare max. 15 gocce in 50ml di liquido p.es. olio di mandorla. Come bagnoschiuma: aggiungere 8-15 gocce versare nell acqua del bagno.</p>
      <p class="usage-block"><strong>Ingredients:</strong> Lavandula angustifolia oil, Limonene*, Linalool*, geraniol*<br>*natürliche Bestandteile des etherischen Öls<br>* Olio essenziale con sostanze naturali</p>
    </div>
    <div class="column column--usage usage-de">
      <p class="usage-block"><strong>100% natürliches etherisches Öl.</strong><br>Aroma-Kosmetikum zur Körperpflege.</p>
      <p class="usage-block"><strong>Anwendung:</strong> Als Haut- u. Massageöl max 15 Tr. Mit 50 ml z.B. Mandelöl mischen. Als Badezusatz 8-15 Tr. Auf 4 Eßl. Sahne oder Milch ins Badewasser geben.</p>
    </div>
  </section>
</div>
</body>
</html>
```